Lo Mara Menu Design Project

This project is pretty straight forward. You will be given 3 files which include the following:
1. Our proposed menu
2. Our Company logo
3. A sample menu on what we are looking for design wise

Your job is to create a visually pleasing menu that is simple, clean and fresh. Please refer to our home website for additional information. (www.lomara-eats.com) Must be in eps or equivalent format.

Target Market(s)

20s to 40s

Industry/Entity Type

It Company

Requirements
Must have
• Company log
Must be in EPS format

```html
<!DOCTYPE html>
<html lang="en">
<head>
<meta charset="utf-8">
<title>Lo Mara Menu</title>
<link rel="stylesheet" href="https://fonts.googleapis.com/css2?family=Arimo:wght@400;700&family=Tinos:wght@700&display=swap">
<style>
  :root {
    --menu-black: #141414;
    --menu-grain: #1f1f1f;
    --menu-deep: #0b0b0b;
    --text-white: #ffffff;
    --text-soft: #e6e6e6;
    --accent-red: #d8231f;
  }
  html, body {
    margin: 0;
    padding: 0;
    width: 985px;
    height: 1200px;
    overflow: hidden;
    background: var(--menu-black);
  }
  .menu {
    position: relative;
    width: 985px;
    height: 1200px;
    overflow: hidden;
    color: var(--text-white);
    font-family: "Arimo", Arial, sans-serif;
  }
  .menu-texture {
    position: absolute;
    inset: 0;
    background: linear-gradient(90deg, var(--menu-deep) 0%, var(--menu-grain) 30%, var(--menu-black) 55%, var(--menu-grain) 80%, var(--menu-deep) 100%);
  }
  .section-title {
    position: absolute;
    left: 0;
    width: 985px;
    margin: 0;
    text-align: center;
    font-family: "Arimo", Arial, sans-serif;
    font-weight: 400;
    font-size: 50px;
    letter-spacing: 0.5px;
    line-height: 1;
  }
  .section-rule {
    position: absolute;
    left: 379px;
    width: 227px;
    height: 4px;
    background: var(--accent-red);
  }
  .dish {
    position: absolute;
    width: 330px;
    margin-left: -165px;
    text-align: center;
  }
  .dish-name, .dish-price {
    font-family: "Tinos", "Times New Roman", serif;
    font-weight: 700;
    font-size: 19px;
    line-height: 24px;
    margin: 0;
  }
  .dish-desc {
    font-size: 15px;
    line-height: 19px;
    color: var(--text-soft);
    margin: 10px 0 0;
  }
  .combo {
    position: absolute;
    left: 0;
    top: 996px;
    width: 985px;
    text-align: center;
  }
  .combo .dish-desc { margin-top: 12px; }
  .brand-name {
    position: absolute;
    right: 45px;
    top: 1098px;
    margin: 0;
    font-family: "Arimo", Arial, sans-serif;
    font-weight: 700;
    font-size: 30px;
    color: var(--accent-red);
    line-height: 1;
    white-space: nowrap;
  }
</style>
</head>
<body>
<main class="menu">
  <div class="menu-texture"></div>

  <h1 class="section-title" style="top:90px">DIM SUM</h1>
  <div class="section-rule" style="top:140px"></div>

  <section class="dish" style="left:172px; top:182px">
    <p class="dish-name">Pan-Fried Potstickers</p>
    <p class="dish-price">$ 6.50</p>
    <p class="dish-desc">Five pan-Fried potstickers with<br>chicken or pork.<br>Served with apricot dipping sauce</p>
  </section>
  <section class="dish" style="left:172px; top:334px">
    <p class="dish-name">Spring Rolls</p>
    <p class="dish-price">$ 4.50</p>
    <p class="dish-desc">Two chicken or vegetable<br>spring rolls. Served with apricot<br>dipping sauce</p>
  </section>
  <section class="dish" style="left:172px; top:498px">
    <p class="dish-name">Shrimp Toast</p>
    <p class="dish-price">$ 5.95</p>
    <p class="dish-desc">Four pieces of fried toast with<br>shrimp, onions, bamboo shoots, and<br>water chestnuts. Served with apricot<br>dipping sauce.</p>
  </section>

  <section class="dish" style="left:492px; top:235px">
    <p class="dish-name">Szechuan Dumplings</p>
    <p class="dish-price">$ 6.25</p>
    <p class="dish-desc">Five chicken dumplings<br>tossed in a spicy cilantro<br>sauce.</p>
  </section>
  <section class="dish" style="left:492px; top:389px; width:400px; margin-left:-200px">
    <p class="dish-name">Wonton Stars</p>
    <p class="dish-price">$ 7.25</p>
    <p class="dish-desc">Five crispy wonton skins filled<br>with real crab and seasoned cream cheese.<br>Served with sweet and sour dipping sauce.</p>
  </section>
  <section class="dish" style="left:492px; top:548px">
    <p class="dish-name">Shu Mai</p>
    <p class="dish-price">$ 5.95</p>
    <p class="dish-desc">Six steamed open-Face dumplings<br>with pork<br>shrimp, and mushrooms.</p>
  </section>

  <section class="dish" style="left:806px; top:182px">
    <p class="dish-name">Steamed Dumplings</p>
    <p class="dish-price">$ 6.50</p>
    <p class="dish-desc">Five steamed dumplings with<br>chicken, or vegetables.<br>Served with apricot dipping sauce.</p>
  </section>
  <section class="dish" style="left:806px; top:334px">
    <p class="dish-name">Bao</p>
    <p class="dish-price">$ 5.95</p>
    <p class="dish-desc">Three fluffy steamed chinese<br>buns filled with barbeque<br>pork.</p>
  </section>
  <section class="dish" style="left:806px; top:498px">
    <p class="dish-name">Gift Wrapped Chicken</p>
    <p class="dish-price">$5.95</p>
    <p class="dish-desc">Six chicken breast tenders marinated<br>in soy sauce<br>sesame oil, and cilantro.</p>
  </section>

  <h1 class="section-title" style="top:714px">STARTERS</h1>
  <div class="section-rule" style="top:762px"></div>

  <section class="dish" style="left:172px; top:823px">
    <p class="dish-name">Lightly Battered Calamari Strips</p>
    <p class="dish-price">$ 5.95</p>
    <p class="dish-desc">Six calamari strips, lightly battered<br>with a garlic ginger aioli.</p>
  </section>
  <section class="dish" style="left:492px; top:855px">
    <p class="dish-name">Edamame</p>
    <p class="dish-price">$ 4.00</p>
    <p class="dish-desc">Steamed Soybean Pods.</p>
  </section>
  <section class="dish" style="left:806px; top:823px">
    <p class="dish-name">House Lo Mara Crab Cake's</p>
    <p class="dish-price">$11.95</p>
    <p class="dish-desc">Jumbo lump Maryland crab meat<br>with seasoned<br>with our Lo Mara spice blend.<br>Topped with a kick of spicy aioli.</p>
  </section>

  <section class="combo">
    <p class="dish-name">Dim Sum And Then Sum &nbsp;&nbsp;(Lunch / Dinner)</p>
    <p class="dish-price">$ 14.95 / 18.95</p>
    <p class="dish-desc">Choose three / four half orders: Potstickers, steamed dumplings, szechwan dumplings,<br>spring roll, shrimp toast, chinese chicken salad, hot &amp; sour soup, wonton soup, or mushu,<br>For Shrimp fried rice, beef fried rice, or mushu shrimp, add $1.00.</p>
  </section>

  <p class="brand-name">Lo Mara</p>
</main>
</body>
</html>
```